Business Cards for Internet Security Company

Awesome designers! This is the opportunity to help design cards for a forward thinking network security company. They use threat information gathered from peer groups to make intelligent decisions on what threats are relevant and which arent. ( not that you need this to do designs, but just so you know where they are coming from. ) :-)

We'd like to see a two side design and the deliverables will be in illustrator 4. The logo is attached and the logo colors are attached in the JPG and I've attached a an eps of the logo and icon

Security

```html
<!DOCTYPE html>
<html lang="en">
<head>
<meta charset="utf-8">
<title>Kelmora Business Cards</title>
<link href="https://fonts.googleapis.com/css2?family=Open+Sans:ital,wght@0,400;0,600;0,700;1,400&display=swap" rel="stylesheet">
<style>
  :root {
    --bg: #dfe4ea;
    --card: #f8f9fb;
    --ink: #2a5a78;
    --accent: #3f8ac4;
    --rule: #6f8aa0;
    --shadow: rgba(40, 60, 80, 0.18);
  }
  * { margin: 0; padding: 0; box-sizing: border-box; }
  html, body {
    width: 1200px; height: 1195px; overflow: hidden;
    background: var(--bg);
    font-family: "Open Sans", Arial, sans-serif;
    color: var(--ink);
  }
  .sheet {
    position: relative; width: 1200px; height: 1195px;
    display: flex; flex-direction: column; align-items: center;
    justify-content: center; gap: 34px;
  }
  .card {
    position: relative; width: 960px; height: 548px;
    background: var(--card);
    box-shadow: 0 10px 30px var(--shadow);
    overflow: hidden;
  }
  /* Front */
  .card-front { display: flex; align-items: center; justify-content: center; }
  .brand { display: flex; align-items: center; gap: 26px; }
  .brand-dot {
    width: 96px; height: 96px; border-radius: 50%;
    border: 16px solid var(--accent);
  }
  .brand-name {
    font-weight: 600; font-size: 150px; letter-spacing: -2px;
    color: var(--ink); line-height: 1;
  }
  /* Back */
  .card-back .brand { position: absolute; left: 60px; top: 46px; gap: 16px; }
  .card-back .brand-dot { width: 50px; height: 50px; border-width: 9px; }
  .card-back .brand-name { font-size: 78px; letter-spacing: -1px; }
  .person { position: absolute; left: 60px; top: 176px; }
  .person-name { font-weight: 700; font-size: 50px; line-height: 1.1; }
  .person-title { font-style: italic; font-size: 40px; line-height: 1.2; white-space: nowrap; }
  .address {
    position: absolute; left: 60px; top: 318px;
    font-size: 32px; line-height: 1.3; white-space: nowrap;
  }
  .contact-line { display: flex; align-items: center; gap: 14px; }
  .contact-line svg { flex: none; }
  .side-contacts {
    position: absolute; left: 520px; top: 318px;
    font-size: 32px; line-height: 1.3; white-space: nowrap;
  }
  .rule {
    position: absolute; left: 60px; right: 50px; height: 2px;
    background: var(--rule);
  }
  .rule-side { top: 418px; left: 520px; }
  .rule-bottom { bottom: 36px; }
</style>
</head>
<body>
<main class="sheet">
  <section class="card card-front" aria-label="Card front">
    <div class="brand">
      <span class="brand-dot"></span>
      <span class="brand-name">Kelmora</span>
    </div>
  </section>

  <section class="card card-back" aria-label="Card back">
    <div class="brand">
      <span class="brand-dot"></span>
      <span class="brand-name">Kelmora</span>
    </div>

    <div class="person">
      <div class="person-name">Dana Whitlock</div>
      <div class="person-title">Chief Executive Officer &amp; Co-Founder</div>
    </div>

    <div class="address">
      <div>418 Meridian Park Dr</div>
      <div>Springfield, MO 65801</div>
      <div class="contact-line">
        <svg width="20" height="30" viewBox="0 0 20 30" aria-hidden="true">
          <rect x="2" y="2" width="16" height="26" rx="3" fill="none" stroke="currentColor" stroke-width="3"/>
          <rect x="6" y="7" width="8" height="8" fill="currentColor"/>
        </svg>
        <span>555-014-2718</span>
      </div>
    </div>

    <div class="side-contacts">
      <div class="contact-line">
        <svg width="36" height="30" viewBox="0 0 36 30" aria-hidden="true">
          <rect x="9" y="2" width="18" height="9" fill="none" stroke="currentColor" stroke-width="3"/>
          <rect x="2" y="11" width="32" height="12" rx="2" fill="none" stroke="currentColor" stroke-width="3"/>
          <rect x="9" y="19" width="18" height="9" fill="var(--card)" stroke="currentColor" stroke-width="3"/>
        </svg>
        <span>555-014-3390</span>
      </div>
      <div class="contact-line">
        <svg width="36" height="26" viewBox="0 0 36 26" aria-hidden="true">
          <rect x="2" y="2" width="32" height="22" fill="none" stroke="currentColor" stroke-width="3"/>
          <path d="M2 2 L18 15 L34 2 M2 24 L14 12 M34 24 L22 12" fill="none" stroke="currentColor" stroke-width="3"/>
        </svg>
        <span>dana@kelmora.com</span>
      </div>
    </div>

    <div class="rule rule-side"></div>
    <div class="rule rule-bottom"></div>
  </section>
</main>
</body>
</html>
```